Brambleton Pizza Website

We are working with Brambleton Pizza and designing them a website.

Some sites to use for content/competitors and inspiration:

https://fennimores.com
https://www.bhq-eats.com
https://brightorchard.com/en-us/

Thank you for taking the time to consider designing a website for us. We are web developers based in Stockton, CA, USA. Most of our projects go through the same process. Understanding this process may help you win a project with us. We custom-code all of our websites in-house. We don’t have any requirements as to what tools you use for your design, but we prefer Figma files. For any design that we label as four-stars, we send it to the client for review. The client picks the final design they want us to use. Once we complete this process, we will continue to show additional clients all the four-star sites and purchase them later. Your designs will have multiple chances to sell. For better chances of success, we ask that you follow these guidelines.

IMAGES:
If you use any images or icons in the design, we ask that you have a link to the asset so we can purchase the image/icon. Most of the designs we submit do not have the customer’s images on them unless they have some great images. Be creative; show us the feeling you are trying to portray with your image choices. Use any royalty-free site you choose. We subscribe to Quillstone and mainly use their images, but we can purchase images outside of Quillstone.

PLEASE NOTE: we will not submit designs to clients with watermarks on the images.

FONTS:
We ask that you identify the fonts used in the design. This can be done in a message if you want. We typically use Google Fonts and Quillstone Fonts.

CONTENT:
We're always open to different content and ideas. We often submit designs with stock images so the client can see our vision. We typically take pictures after the website launch to use their images with our vision. Lorem Ipsum is fine for paragraphs, but we ask that you write the headers in correct English. We want to be able to show the vision and identify the sections of the website.

INSPIRATION:
We typically add a couple of links in the brief of websites we like to help you get started in your design.

REVISIONS:
We do not often ask for revisions of the designs unless we see something in the design that may not appeal to the client. If there are slight changes that we want to make, we do that in the development process.

FEEDBACK:
We rarely give feedback on designs during the design process. We are working on many website projects and do not have the time to provide feedback. We usually respond if your request is well thought out and asks specific questions, but a note asking “feedback, please” usually goes unanswered.

```html
<!DOCTYPE html>
<html lang="en">
<head>
<meta charset="utf-8">
<title>Brambleton Pizza</title>
<link rel="stylesheet" href="https://fonts.googleapis.com/css2?family=Bebas+Neue&family=Yellowtail&family=Roboto:wght@400;500;700&display=swap">
<style>
:root{
  --red:#e42a2a;
  --red-dark:#c81f1f;
  --green:#33a83a;
  --green-dark:#2a9431;
  --ink:#222222;
  --wood:#2a2826;
  --wood-dark:#1c1b1a;
  --paper:#e9e9e8;
  --paper-light:#f2f2f1;
  --white:#ffffff;
}
*{margin:0;padding:0;box-sizing:border-box}
html,body{width:1200px;height:4769px;overflow:hidden}
body{position:relative;font-family:"Roboto",Arial,sans-serif;color:var(--ink);background:var(--white)}
.abs{position:absolute}
.display{font-family:"Bebas Neue",Impact,sans-serif;font-weight:400;letter-spacing:.5px;line-height:.95}
.script{font-family:"Yellowtail",cursive;color:var(--red)}
.btn{position:absolute;display:flex;align-items:center;justify-content:center;border-radius:26px;color:var(--white);font-weight:700;font-size:17px;text-transform:uppercase;box-shadow:0 3px 0 rgba(0,0,0,.18)}
.btn-red{background:var(--red)}
.btn-green{background:var(--green)}
.btn-black{background:#111}
.price-badge{position:absolute;width:124px;height:124px;border-radius:50%;background:var(--green);border:5px solid var(--white);color:var(--white);display:flex;align-items:center;justify-content:center;font-family:"Bebas Neue",Impact,sans-serif;font-size:50px;box-shadow:0 4px 10px rgba(0,0,0,.2)}

/* header */
.topbar{left:0;top:0;width:1200px;height:89px;background:var(--white)}
.navbar{left:0;top:89px;width:1200px;height:68px;background:var(--red)}
.nav-link{position:absolute;top:107px;color:var(--white);font-family:"Bebas Neue",Impact,sans-serif;font-size:24px;letter-spacing:1px}
.brand-badge{left:112px;top:14px;width:230px;height:196px;background:var(--white);border-radius:0 0 115px 115px;display:flex;flex-direction:column;align-items:center;justify-content:center;gap:10px}
.brand-dot{width:46px;height:46px;border-radius:50%;background:var(--red)}
.brand-name{font-family:"Bebas Neue",Impact,sans-serif;color:var(--ink);font-size:40px;line-height:.9;text-align:center}

/* hero */
.hero{left:0;top:157px;width:1200px;height:583px;background:linear-gradient(90deg,var(--wood-dark),var(--wood) 40%,var(--wood-dark));overflow:hidden}

/* about */
.about{left:0;top:740px;width:1200px;height:650px;background:var(--red)}

/* menu */
.menu{left:0;top:1390px;width:1200px;height:1207px;background:radial-gradient(ellipse at 40% 40%,var(--paper-light),var(--paper) 70%,#dcdcdb)}
.dish-label{position:absolute;font-family:"Bebas Neue",Impact,sans-serif;font-size:37px;line-height:1.1;color:var(--ink)}

/* fundraising */
.fundraise{left:0;top:2597px;width:1200px;height:568px;background:var(--green);overflow:hidden}

/* specials */
.specials{left:0;top:3165px;width:1200px;height:765px;background:var(--paper)}
.special-card{position:absolute;top:3367px;width:292px;height:453px;background:var(--white)}
.special-photo{width:292px;height:233px}
.special-price{margin-top:36px;text-align:center;font-family:"Bebas Neue",Impact,sans-serif;color:var(--green);font-size:40px}
.special-text{margin-top:8px;text-align:center;font-weight:700;font-size:17px;line-height:1.3;text-transform:uppercase}
.special-card .btn{left:78px;top:374px;width:136px;height:44px;font-size:15px}

/* order band */
.order-band{left:0;top:3930px;width:1200px;height:340px;background:radial-gradient(ellipse at 30% 60%,#b07a4a,#6e4a2a 45%,#3c3a24 80%)}

/* footer */
.footer{left:0;top:4270px;width:1200px;height:499px;background:linear-gradient(90deg,var(--wood-dark),var(--wood) 50%,var(--wood-dark))}
.foot-title{position:absolute;top:4362px;color:var(--white);font-family:"Bebas Neue",Impact,sans-serif;font-size:34px}
.foot-list{position:absolute;top:4422px;list-style:none;color:var(--white);font-size:15px;line-height:35px}
.contact-row{position:absolute;left:822px;display:flex;gap:12px;color:var(--white);font-size:15px;line-height:1.5}
.contact-row svg{flex:none;margin-top:3px}
</style>
</head>
<body>

<!-- Header -->
<div class="abs topbar"></div>
<div class="abs navbar"></div>
<a class="btn btn-black" style="left:532px;top:20px;width:150px;height:50px;">
  <svg width="16" height="16" viewBox="0 0 24 24" style="margin-right:8px"><path fill="#fff" d="M6.6 10.8a15 15 0 0 0 6.6 6.6l2.2-2.2c.3-.3.7-.4 1-.2 1.1.4 2.3.6 3.6.6.6 0 1 .4 1 1V20c0 .6-.4 1-1 1A17 17 0 0 1 3 4c0-.6.4-1 1-1h3.5c.6 0 1 .4 1 1 0 1.3.2 2.5.6 3.6.1.3 0 .7-.2 1z"/></svg>Call Now</a>
<a class="btn btn-red" style="left:698px;top:20px;width:150px;height:50px;">Order Now</a>
<a class="btn btn-green" style="left:858px;top:20px;width:214px;height:50px;">Delivery &amp; Pickup</a>
<nav>
  <span class="nav-link" style="left:437px">Home</span>
  <span class="nav-link" style="left:527px">Menu</span>
  <span class="nav-link" style="left:615px">Catering</span>
  <span class="nav-link" style="left:733px">Today's Deals</span>
  <span class="nav-link" style="left:892px">Locations</span>
  <span class="nav-link" style="left:1018px">Sign In</span>
</nav>

<!-- Hero -->
<section class="abs hero">
  <svg class="abs" style="left:0;top:0" width="1200" height="583" role="img" aria-label="Photo of a fresh pizza with peppers, spinach and red onion on a wooden board">
    <defs>
      <radialGradient id="heroPizza" cx="55%" cy="40%" r="60%">
        <stop offset="0" stop-color="#d9752f"/>
        <stop offset=".55" stop-color="#c4562a"/>
        <stop offset=".8" stop-color="#e0b474"/>
        <stop offset="1" stop-color="#8a5a32"/>
      </radialGradient>
    </defs>
    <circle cx="1010" cy="363" r="540" fill="url(#heroPizza)" stroke="#fff" stroke-width="4"/>
  </svg>
  <div class="abs script" style="left:128px;top:120px;font-size:34px;">Welcome to</div>
  <h1 class="abs display" style="left:126px;top:162px;color:var(--white);font-size:80px;line-height:.99;">Brambleton<br>Italian Fresh<br>Pizza</h1>
  <div class="abs" style="left:262px;top:326px;width:64px;height:64px;border-radius:50%;background:var(--green);border:3px solid #fff;color:#fff;display:flex;align-items:center;justify-content:center;font-family:'Bebas Neue',Impact,sans-serif;font-size:30px;">$56</div>
  <a class="btn btn-red" style="left:126px;top:425px;width:152px;height:50px;">Order Now</a>
</section>

<!-- About -->
<section class="abs about">
  <div class="abs" style="left:100px;top:140px;width:490px;height:360px;display:flex;flex-direction:column;align-items:center;justify-content:center;gap:24px;">
    <div style="width:70px;height:70px;border-radius:50%;background:var(--white)"></div>
    <div class="display" style="color:var(--white);font-size:96px;text-align:center;line-height:.9;">Brambleton<br>Pizza</div>
  </div>
  <div class="abs script" style="left:672px;top:112px;font-size:36px;color:var(--white);">About Us</div>
  <h2 class="abs display" style="left:670px;top:160px;font-size:76px;color:var(--white);">Brambleton Pizza</h2>
  <p class="abs" style="left:670px;top:255px;width:410px;font-size:19px;line-height:1.25;color:var(--white);">Lorem ipsum dolor sit amet, loreconsectetur adipis cing elit, sed do eiusmod tempor incid idunt ut labore et dolore magna aliqua. Quis ipsum suspendisse ultrices gravida. Risus commodo viverra maecenas acculoremsan lacus vel faciluspendisse ultrices gravida. Risus commodo viverra maecenas accum san lacus vel facilisis.</p>
  <a class="btn btn-green" style="left:672px;top:475px;width:160px;height:50px;">Read More</a>
</section>

<!-- Menu highlights -->
<section class="abs menu">
  <div class="abs script" style="left:128px;top:170px;font-size:34px;color:var(--ink);">Let's Eat</div>
  <h2 class="abs display" style="left:124px;top:214px;font-size:76px;color:var(--red);">Brambleton Pizza</h2>
  <p class="abs" style="left:129px;top:312px;width:420px;font-size:16.5px;line-height:1.28;">Lorem ipsum dolor sit amet, consectetur adipiscing elit, sed do eiusmod tempor incididunt ut labore et dolore magna aliqua. Quis ipsum suspendisse ultrices gravida. Risus commodo viverra maecenas accumsan lacus vel facilisis.</p>

  <svg class="abs" style="left:685px;top:135px" width="390" height="430" role="img" aria-label="Photo of a stuffed pizza with olives and mozzarella">
    <defs><linearGradient id="stuffed" x1="0" y1="0" x2="1" y2="1"><stop offset="0" stop-color="#c94a2a"/><stop offset=".5" stop-color="#e0a456"/><stop offset="1" stop-color="#7a3a1e"/></linearGradient></defs>
    <path d="M10 125 Q195 -45 380 125 L215 430 Z" fill="url(#stuffed)"/>
  </svg>
  <div class="dish-label" style="left:626px;top:442px;">Famous<br>Stuffed Pizza</div>
  <div class="price-badge" style="left:903px;top:390px;">$56</div>

  <div class="dish-label" style="left:137px;top:525px;">Hand-Stretched<br>Thin Crust</div>
  <div class="price-badge" style="left:408px;top:535px;">$56</div>
  <svg class="abs" style="left:265px;top:625px" width="335" height="340" role="img" aria-label="Photo of a sliced thin crust pizza with mushrooms, tomatoes and basil">
    <defs><radialGradient id="thin" cx="50%" cy="50%" r="50%"><stop offset="0" stop-color="#d66a33"/><stop offset=".75" stop-color="#e7a75a"/><stop offset="1" stop-color="#c98a44"/></radialGradient></defs>
    <circle cx="167" cy="170" r="162" fill="url(#thin)"/>
  </svg>

  <svg class="abs" style="left:740px;top:650px" width="390" height="425" role="img" aria-label="Photo of a classic Italian pizza slice with melted cheese and red onion">
    <defs><linearGradient id="classic" x1="0" y1="0" x2="1" y2="1"><stop offset="0" stop-color="#e8cf9c"/><stop offset=".5" stop-color="#d79a5a"/><stop offset="1" stop-color="#5a4a2e"/></linearGradient></defs>
    <path d="M10 125 Q195 -45 380 125 L200 425 Z" fill="url(#classic)"/>
  </svg>
  <div class="dish-label" style="left:682px;top:955px;">Classic<br>Italian</div>
  <div class="price-badge" style="left:958px;top:903px;">$56</div>
</section>

<!-- Fundraising -->
<section class="abs fundraise">
  <svg class="abs" style="left:530px;top:0" width="670" height="568" role="img" aria-label="Photo of a loaded pizza with ham, tomatoes, olives and basil on a wooden table">
    <defs>
      <linearGradient id="fundFade" x1="0" y1="0" x2="1" y2="0"><stop offset="0" stop-color="#33a83a"/><stop offset=".25" stop-color="#6a6a36"/><stop offset="1" stop-color="#5a3b22"/></linearGradient>
      <radialGradient id="fundPizza" cx="50%" cy="50%" r="50%"><stop offset="0" stop-color="#c9482e"/><stop offset=".8" stop-color="#d99a52"/><stop offset="1" stop-color="#b87838"/></radialGradient>
    </defs>
    <rect width="670" height="568" fill="url(#fundFade)"/>
    <ellipse cx="320" cy="275" rx="300" ry="250" fill="url(#fundPizza)"/>
  </svg>
  <h2 class="abs display" style="left:126px;top:158px;font-size:64px;color:var(--white);line-height:1;">Fundraising Made<br>Deliciously Easy</h2>
  <p class="abs" style="left:129px;top:303px;font-size:19px;font-weight:700;line-height:1.25;color:var(--white);">LOREM IPSUM DOLOR SIT AMET,<br>CONS ECTETUR ADIPISCING.</p>
  <a class="btn btn-red" style="left:130px;top:375px;width:160px;height:48px;">Buy Now</a>
</section>

<!-- Specials -->
<section class="abs specials">
  <h2 class="display" style="position:absolute;left:0;top:92px;width:1200px;text-align:center;font-size:80px;color:var(--red);">Our Specials</h2>
</section>
<article class="special-card" style="left:126px;">
  <svg class="special-photo" role="img" aria-label="Photo of a take and bake pizza with olive oil and tomatoes"><defs><radialGradient id="sp1" cx="45%" cy="55%" r="60%"><stop offset="0" stop-color="#d0602e"/><stop offset=".6" stop-color="#9a5a30"/><stop offset="1" stop-color="#2e2620"/></radialGradient></defs><rect width="292" height="233" fill="url(#sp1)"/></svg>
  <div class="special-price">$19.00</div>
  <div class="special-text">Take &amp; Bake Always<br>Oven Fresh</div>
  <a class="btn btn-red">Order Now</a>
</article>
<article class="special-card" style="left:454px;">
  <svg class="special-photo" role="img" aria-label="Photo of a cheesy pizza slice being lifted"><defs><linearGradient id="sp2" x1="0" y1="0" x2="0" y2="1"><stop offset="0" stop-color="#3a2a22"/><stop offset=".5" stop-color="#e6c27a"/><stop offset="1" stop-color="#b86a30"/></linearGradient></defs><rect width="292" height="233" fill="url(#sp2)"/></svg>
  <div class="special-price">$19.00</div>
  <div class="special-text">Lorem I Dolor Sit<br>Ameonsectur.</div>
  <a class="btn btn-red">Order Now</a>
</article>
<article class="special-card" style="left:781px;">
  <svg class="special-photo" role="img" aria-label="Photo of a sliced pizza with herbs on a pan"><defs><radialGradient id="sp3" cx="50%" cy="50%" r="60%"><stop offset="0" stop-color="#b0563a"/><stop offset=".7" stop-color="#7a4a32"/><stop offset="1" stop-color="#3a3a3a"/></radialGradient></defs><rect width="292" height="233" fill="url(#sp3)"/></svg>
  <div class="special-price">$19.00</div>
  <div class="special-text">Lorem I Dolor Sit<br>Ameonsectur.</div>
  <a class="btn btn-red">Order Now</a>
</article>

<!-- Start your order -->
<section class="abs order-band" role="img" aria-label="Blurred close-up photo of pizza toppings">
  <h2 class="display" style="position:absolute;left:0;top:88px;width:1200px;text-align:center;font-size:74px;color:var(--white);">Start Your Order</h2>
  <a class="btn btn-green" style="left:461px;top:185px;width:136px;height:48px;">Delivery</a>
  <a class="btn btn-green" style="left:608px;top:185px;width:132px;height:48px;">Pickup</a>
</section>

<!-- Footer -->
<footer class="abs footer"></footer>
<div class="foot-title" style="left:126px;">Links</div>
<ul class="foot-list" style="left:126px;">
  <li>Our Story</li><li>Events</li><li>Blog</li><li>Press</li><li>Talk To Us</li>
</ul>
<ul class="foot-list" style="left:246px;">
  <li>Gift Cards</li><li>Ship A Frozen Pizza</li><li>Delivery &amp; Pickup</li><li>Join Our Team</li><li>Specials</li>
</ul>
<div class="abs" style="left:460px;top:4380px;width:280px;height:220px;display:flex;flex-direction:column;align-items:center;justify-content:center;gap:16px;">
  <div style="width:50px;height:50px;border-radius:50%;background:var(--red)"></div>
  <div class="display" style="color:var(--white);font-size:62px;text-align:center;line-height:.9;">Brambleton<br>Pizza</div>
</div>
<div class="foot-title" style="left:822px;">Contact Us</div>
<div class="contact-row" style="top:4425px;">
  <svg width="16" height="18" viewBox="0 0 24 24"><path fill="#e42a2a" d="M12 2a7 7 0 0 0-7 7c0 5 7 13 7 13s7-8 7-13a7 7 0 0 0-7-7zm0 9.5A2.5 2.5 0 1 1 12 6a2.5 2.5 0 0 1 0 5.5z"/></svg>
  <span>22950 dumy Lorems 78<br>Dummy, Placeholder 48220</span>
</div>
<div class="contact-row" style="top:4485px;">
  <svg width="16" height="16" viewBox="0 0 24 24"><path fill="#e42a2a" d="M6.6 10.8a15 15 0 0 0 6.6 6.6l2.2-2.2c.3-.3.7-.4 1-.2 1.1.4 2.3.6 3.6.6.6 0 1 .4 1 1V20c0 .6-.4 1-1 1A17 17 0 0 1 3 4c0-.6.4-1 1-1h3.5c.6 0 1 .4 1 1 0 1.3.2 2.5.6 3.6.1.3 0 .7-.2 1z"/></svg>
  <span>Phone (555) 014-2280</span>
</div>
<div class="contact-row" style="top:4520px;">
  <svg width="16" height="16" viewBox="0 0 24 24"><path fill="#e42a2a" d="M3 5h18v14H3zm2 2v.5l7 4.5 7-4.5V7z"/></svg>
  <span>eat@BrambletonPizza.com</span>
</div>
<div class="contact-row" style="top:4555px;">
  <svg width="16" height="16" viewBox="0 0 24 24"><circle cx="12" cy="12" r="10" fill="#e42a2a"/><path d="M12 6v6l4 2" stroke="#fff" stroke-width="2" fill="none"/></svg>
  <span>Sat. - Sun. 8 a.m. - 3 p.m.</span>
</div>
<div class="abs" style="left:126px;top:4625px;width:946px;height:1px;background:rgba(255,255,255,.25);"></div>
<div class="abs" style="left:560px;top:4642px;width:36px;height:36px;border-radius:50%;border:2px solid var(--red);"></div>
<div class="abs" style="left:604px;top:4642px;width:36px;height:36px;border-radius:50%;border:2px solid var(--red);"></div>
<p class="abs" style="left:0;top:4716px;width:1200px;text-align:center;color:var(--white);font-size:14px;">© 2025 All Rights Reserved. Terms &amp; Conditions Privacy Policy</p>

</body>
</html>
```